Design and Renovation Company Luxury Business Card

I want to create a luxury business card for a Design and Renovation Firm . We will use our current logo. The company name is 528BUILDA. We do not want anything standard. We need a very unique concept.
Please see uploaded inspiration. I really like the textured paper option. I would like the card to be thick with debossing, and/or embossing options. The logo has orange in it but I would like to see the card with and without the orange. I think the orange may make the company feel less high-end. The goal is to elevate the logo not match its vibe per se of the logo. We want something very unique, not standard at all!
I would like a space for :
Logo,
Name,
Position,
Email,
Office number,
Website Address,
Business Address,
Thank you!
Have fun!
Target Market(s)
Home owners Age 35 +
Industry/Entity Type
Design and Renovation
Contact Information for Business Card
Logo, Name, Position, Email, Office number, Website Address, Business Address,.
Colors
Designer to choose colors to be used in the design.
Requirements
Must have
- A luxury designer feel. Must be black or dark grey but open to other luxury ideas.
Nice to have
- Gold, silver, black embossing or debossing. Textured paper design.
Should not have
- A cheap look and feel.

```html
<!DOCTYPE html>
<html lang="en">
<head>
<meta charset="utf-8">
<title>528BUILDA Business Card</title>
<link rel="stylesheet" href="https://fonts.googleapis.com/css2?family=Montserrat:wght@400;700&display=swap">
<style>
  :root {
    --stage: #9d9d9d;
    --paper: #ffffff;
    --ink: #141414;
    --ink-back: #1a1a1a;
    --accent: #f7941d;
    --text-light: #ffffff;
    --text-dark: #111111;
  }
  * { margin: 0; padding: 0; box-sizing: border-box; }
  html, body {
    width: 1093px;
    height: 1200px;
    overflow: hidden;
    background: var(--stage);
  }
  .card {
    position: absolute;
    left: 264px;
    width: 597px;
    height: 363px;
    border-radius: 18px;
    overflow: hidden;
  }
  .card--front { top: 225px; background: var(--paper); }
  .card--back  { top: 616px; background: var(--ink-back); }

  .wave { position: absolute; inset: 0; width: 100%; height: 100%; }
  .wave .band { fill: var(--accent); }
  .wave .base { fill: var(--ink); }

  .brand {
    display: flex;
    align-items: center;
    font-family: "Montserrat", sans-serif;
    font-weight: 700;
    line-height: 1;
  }
  .brand__dot {
    flex: none;
    border-radius: 50%;
    background: var(--accent);
  }
  .brand--front {
    position: absolute;
    right: 60px;
    top: 120px;
    gap: 10px;
    font-size: 28px;
    color: var(--text-dark);
  }
  .brand--front .brand__dot { width: 18px; height: 18px; }
  .brand--back {
    position: absolute;
    left: 0;
    right: 0;
    top: 157px;
    justify-content: center;
    gap: 14px;
    font-size: 46px;
    color: var(--text-light);
  }
  .brand--back .brand__dot { width: 26px; height: 26px; }

  .person {
    position: absolute;
    left: 27px;
    top: 195px;
    font-family: "Montserrat", sans-serif;
  }
  .person__name {
    font-weight: 700;
    font-size: 24px;
    color: var(--accent);
    line-height: 1.1;
  }
  .person__role {
    font-weight: 400;
    font-size: 15px;
    color: var(--text-light);
    margin-top: 3px;
  }

  .contact {
    position: absolute;
    left: 27px;
    top: 272px;
    list-style: none;
    font-family: "Montserrat", sans-serif;
    font-size: 15px;
    color: var(--text-light);
  }
  .contact li {
    display: flex;
    align-items: center;
    height: 23.5px;
  }
  .contact svg {
    width: 14px;
    height: 14px;
    margin-right: 7px;
    fill: var(--accent);
    flex: none;
  }

  .address {
    position: absolute;
    left: 389px;
    top: 305px;
    font-family: "Montserrat", sans-serif;
    font-style: normal;
    font-size: 15px;
    line-height: 17px;
    color: var(--text-light);
  }
</style>
</head>
<body>

<section class="card card--front">
  <svg class="wave" viewBox="0 0 1002 610" preserveAspectRatio="none" aria-hidden="true">
    <path class="band" d="M0,322 C70,270 130,262 180,262 C330,262 450,350 560,402 C650,446 700,462 752,462 C860,462 945,400 1002,328 L1002,610 L0,610 Z"/>
    <path class="base" d="M0,345 C70,292 130,284 180,284 C330,284 450,372 560,424 C650,468 700,480 752,480 C860,480 945,420 1002,350 L1002,610 L0,610 Z"/>
  </svg>

  <div class="brand brand--front">
    <span class="brand__dot"></span>
    <span class="brand__name">528BUILDA</span>
  </div>

  <div class="person">
    <p class="person__name">Daniel Harper</p>
    <p class="person__role">Managing Director</p>
  </div>

  <ul class="contact">
    <li>
      <svg viewBox="0 0 24 24" aria-hidden="true"><path d="M6.6 10.8a15.1 15.1 0 0 0 6.6 6.6l2.2-2.2a1 1 0 0 1 1-.25 11.4 11.4 0 0 0 3.6.57 1 1 0 0 1 1 1V20a1 1 0 0 1-1 1A17 17 0 0 1 3 4a1 1 0 0 1 1-1h3.5a1 1 0 0 1 1 1c0 1.25.2 2.45.57 3.57a1 1 0 0 1-.25 1z"/></svg>
      704-555-0148
    </li>
    <li>
      <svg viewBox="0 0 24 24" aria-hidden="true"><path d="M2 5h20v2l-10 6L2 7z M2 9l10 6 10-6v10H2z"/></svg>
      info@528builda.com
    </li>
    <li>
      <svg viewBox="0 0 24 24" aria-hidden="true"><path d="M12 2a10 10 0 1 0 0 20 10 10 0 0 0 0-20zm-1 17.9A8 8 0 0 1 4.2 10.2L9 15v1a2 2 0 0 0 2 2zm6.9-2.5A2 2 0 0 0 16 16h-1v-3a1 1 0 0 0-1-1H8v-2h2a1 1 0 0 0 1-1V7h2a2 2 0 0 0 2-2v-.4a8 8 0 0 1 2.9 12.8z"/></svg>
      www.528builda.com
    </li>
  </ul>

  <address class="address">
    415 Maple Grove Ave, #112<br>
    Lakeview, OH 43210
  </address>
</section>

<section class="card card--back">
  <div class="brand brand--back">
    <span class="brand__dot"></span>
    <span class="brand__name">528BUILDA</span>
  </div>
</section>

</body>
</html>
```